Business card for my new company (Accounting firm)

I need a business card for my new business Brightwell Advisory and Ledger SA. Our services are accounting, tax, audit and financial management. Our customers are small companies, start-ups and new companies. The final design has to show financial security, trust and growth. Please find our logo attached to the business card. Text for the business card: Brightwell Advisory and Ledger SA Tomas Varenholt Director and Founder Certified Accountant Tel. 022 418 57 34 tv@clairevalconseil.ch www.clairevalconseil.ch Rue des Vergières 27 1201 Geneva
Target Market(s)
Our customers are small companies, start-ups and new companies.
Industry/Entity Type
Finance And Accounting
Contact Information for Business Card
Claireval Conseil et Comptes SA
Tomas Varenholt
Directeur et Fondateur
Expert-comptable diplômé
Tél. 022 418 57 34
tv@clairevalconseil.ch
www.clairevalconseil.ch
Rue des Vergières 27
1201 Genève

```html
<!DOCTYPE html>
<html lang="fr">
<head>
<meta charset="utf-8">
<title>Claireval Conseil et Comptes SA – Carte de visite</title>
<link href="https://fonts.googleapis.com/css2?family=Roboto:wght@400;500;700&display=swap" rel="stylesheet">
<style>
  :root{
    --bg:#e4e5e7;
    --paper:#ffffff;
    --paper-soft:#f1f2f3;
    --blue:#1b6fa8;
    --blue-deep:#175f93;
    --blue-light:#2ea3da;
    --ink:#3a3b3d;
    --arc:#2f3033;
    --on-blue:#ffffff;
  }
  *{box-sizing:border-box;margin:0;padding:0}
  html,body{width:1200px;height:726px;overflow:hidden}
  body{
    background:var(--bg);
    font-family:"Roboto",Arial,sans-serif;
    position:relative;
  }
  .card{
    position:absolute;
    top:205px;
    width:520px;height:316px;
    background:var(--paper);
    box-shadow:0 10px 26px rgba(0,0,0,.14),0 2px 5px rgba(0,0,0,.08);
    overflow:hidden;
  }
  .card--front{left:60px}
  .card--back{left:620px;background:var(--paper-soft)}

  .front-stripe{
    position:absolute;left:0;right:0;bottom:38px;height:6px;
    background:var(--blue-light);
  }
  .brand{
    position:absolute;
    display:flex;flex-direction:column;align-items:center;
    color:var(--ink);font-weight:500;text-align:center;
  }
  .brand__mark{width:34px;height:34px;background:var(--blue);margin-bottom:12px}
  .brand__name{font-size:38px;letter-spacing:4px;line-height:1}
  .brand__tag{font-size:12.5px;letter-spacing:3.2px;margin-top:7px;line-height:1}
  .card--front .brand{left:0;right:0;top:82px}

  .card--back .brand{left:14px;top:104px;width:190px}
  .card--back .brand__mark{width:26px;height:26px;margin-bottom:10px}
  .card--back .brand__name{font-size:26px;letter-spacing:2.5px}
  .card--back .brand__tag{font-size:8.6px;letter-spacing:2px;margin-top:6px}

  .back-panel{position:absolute;inset:0;width:520px;height:316px}

  .contact{
    position:absolute;right:26px;top:30px;
    color:var(--on-blue);text-align:right;
  }
  .contact__name{font-size:21px;font-weight:700;line-height:1.1}
  .contact__role{font-size:11.5px;line-height:1.4;margin-top:4px;opacity:.95}
  .contact__address{font-size:12.5px;line-height:1.45;margin-top:40px;margin-right:20px}
  .contact__lines{list-style:none;margin-top:10px;font-size:12.5px;line-height:1.6}
  .contact__lines li{display:flex;justify-content:flex-end;align-items:center;gap:8px}
  .contact__lines svg{width:12px;height:12px;flex:none}
</style>
</head>
<body>

  <section class="card card--front" aria-label="Recto de la carte">
    <div class="brand">
      <span class="brand__mark"></span>
      <span class="brand__name">CLAIREVAL</span>
      <span class="brand__tag">CONSEIL ET COMPTES</span>
    </div>
    <div class="front-stripe"></div>
  </section>

  <section class="card card--back" aria-label="Verso de la carte">
    <svg class="back-panel" viewBox="0 0 520 316" aria-hidden="true">
      <path d="M178,0 C250,60 286,170 274,316 L520,316 L520,0 Z" fill="var(--arc)"/>
      <path d="M186,0 C258,60 294,170 282,316 L520,316 L520,0 Z" fill="var(--blue)"/>
    </svg>

    <div class="brand">
      <span class="brand__mark"></span>
      <span class="brand__name">CLAIREVAL</span>
      <span class="brand__tag">CONSEIL ET COMPTES</span>
    </div>

    <div class="contact">
      <p class="contact__name">Tomas Varenholt</p>
      <p class="contact__role">Directeur et Fondateur<br>Expert-comptable diplômé</p>
      <p class="contact__address">Rue des Vergières 27<br>1201 Genève</p>
      <ul class="contact__lines">
        <li>022 418 57 34
          <svg viewBox="0 0 12 12"><path d="M2 1.5h2l1 2.5-1.3 1a6 6 0 0 0 3.3 3.3l1-1.3 2.5 1v2A1 1 0 0 1 9.5 11 8.5 8.5 0 0 1 1 2.5a1 1 0 0 1 1-1z" fill="#fff"/></svg>
        </li>
        <li>tv@clairevalconseil.ch
          <svg viewBox="0 0 12 12"><rect x="1" y="2.5" width="10" height="7" fill="#fff"/><path d="M1 2.5 6 6.5 11 2.5" fill="none" stroke="var(--blue)" stroke-width="1"/></svg>
        </li>
        <li>www.clairevalconseil.ch
          <svg viewBox="0 0 12 12"><circle cx="6" cy="6" r="5" fill="#fff"/><path d="M1 6h10M6 1c-2 2.5-2 7.5 0 10M6 1c2 2.5 2 7.5 0 10" fill="none" stroke="var(--blue)" stroke-width=".8"/></svg>
        </li>
      </ul>
    </div>
  </section>

</body>
</html>
```